3D abstract logo Construction, Kitchen and Bath design and Project Management Business Card Design

I want a 3d abstract logo for a new General Construction, Kitchen and Bath design and Project Management Company located at Philadelphia PA, we want to put our logo in the white color trucks too. I want to look professional and serious at the same time look like an architect design and the warm originals color that make you feel in a nice decorated home, I like the colors trend in this link:
http://www.quellmark.example/qm/ggs/pageeditor.aspx?alt_doc_id=RT41K-M9B33-2W5&doc_id=5913046628&pf_id=D4H

I was thinking about a roof and the PA font could have square shape or like wood framing with two tones of the brick color black and creamy yellow color.... Also I like the keystone Idea like the modification or the Ridgeline Parkway logo but curvy at the top

The final design should communicate big company (because we want to grow), responsible, professional and organized that really care about our customers and give them everything they need... plan and design, excellent labor and Project Management
Updates

I doesn't have to be 3d

Reason: I haven't received enough options...

Please stick with the warm tones shown in the image001 attached I like spicy cinnamon instead a cold wine or brick color and also the cream yellowish tones added

Hello designers, please use only the idea and colors of the image001 I don't want to be stick with a house logo because I do commercial construction too so I prefer work around the keystone idea maybe leaving the style of the PA.
I'd like the base tone on the card dark like first option and you can send me a white option too.

Please send me your ideas as soon as possible 

Thank you so much!

Target Market(s)

Builders, State, commercial business owners, Property owners or Real State and Property Management Companies

Industry/Entity Type

Architect

Contact Information for Business Card

RK Buildworks LLC
“Your project is our business”
Lorna Vasquel Eng.
President
Commercial & Residential General Construction
Kitchen & Bath Design | Project Management
Phone: 555-304-7718 | Fax: 555-304-7719 Cell: 555-862-3097
lorna@rkbuildworks.example

```html
<!DOCTYPE html>
<html lang="en">
<head>
<meta charset="utf-8">
<title>RK Buildworks – Business Card Options</title>
<link href="https://fonts.googleapis.com/css2?family=Arimo:ital,wght@0,400;0,700;1,400&display=swap" rel="stylesheet">
<style>
  :root{
    --cinnamon:#a5001a;
    --mustard:#ebb734;
    --cocoa:#45260f;
    --cream:#fffbe6;
    --gold-text:#e8b43a;
    --ink:#1a1a1a;
    --white:#ffffff;
    --orange:#e0601e;
    --rose:#d9415a;
  }
  *{box-sizing:border-box;margin:0;padding:0}
  html,body{width:1200px;height:919px;overflow:hidden;background:var(--white)}
  body{position:relative;font-family:"Arimo",Arial,sans-serif}

  .pair{position:absolute}
  .back{position:absolute;width:228px;height:385px;background:var(--back-bg)}
  .back .mark{position:absolute;left:47px;top:108px;width:132px;height:132px;border-radius:50%;
    background:var(--mark-bg);display:flex;align-items:center;justify-content:center;text-align:center;
    color:var(--mark-ink);font-weight:700;font-size:19px;line-height:1.15}
  .back .tagline{position:absolute;left:38px;top:251px;white-space:nowrap;font-size:12.5px;color:var(--tag-ink)}
  .back .url{position:absolute;left:0;width:228px;top:328px;text-align:center;font-size:10px;color:var(--white)}

  .front{position:absolute;width:386px;height:226px;background:var(--cream);overflow:hidden}
  .front svg{position:absolute;inset:0}
  .front .name{position:absolute;left:19px;top:16px;font-weight:700;font-size:22px;color:var(--name-ink)}
  .front .title{position:absolute;left:20px;top:42px;font-style:italic;font-size:14.5px;color:var(--name-ink)}
  .front .services{position:absolute;left:19px;top:72px;font-size:13px;line-height:15px;color:var(--gold-text)}
  .front .contacts{position:absolute;left:19px;top:147px;font-size:10.5px;line-height:17px;border-collapse:collapse}
  .front .contacts th{text-align:left;font-weight:400;color:var(--label-ink);width:53px}
  .front .contacts td{color:var(--ink)}

  .opt-cinnamon{left:0;top:0;--back-bg:var(--cinnamon);--mark-bg:var(--cream);--mark-ink:var(--cinnamon);--tag-ink:var(--white);--name-ink:var(--cinnamon);--label-ink:var(--cinnamon)}
  .opt-mustard{left:604px;top:2px;--back-bg:var(--mustard);--mark-bg:var(--cinnamon);--mark-ink:var(--cream);--tag-ink:var(--cinnamon);--name-ink:var(--cinnamon);--label-ink:var(--cinnamon)}
  .opt-mustard-light{left:0;top:401px;--back-bg:var(--mustard);--mark-bg:var(--cream);--mark-ink:var(--cinnamon);--tag-ink:var(--white);--name-ink:var(--cinnamon);--label-ink:var(--cinnamon)}
  .opt-cocoa{left:604px;top:404px;--back-bg:var(--cocoa);--mark-bg:var(--cream);--mark-ink:var(--cinnamon);--tag-ink:var(--white);--name-ink:var(--cocoa);--label-ink:var(--gold-text)}

  .opt-cinnamon .front{left:173px;top:107px}
  .opt-mustard .front{left:203px;top:104px}
  .opt-mustard-light .front{left:168px;top:85px}
  .opt-cocoa .front{left:202px;top:80px}
</style>
</head>
<body>

<section class="pair opt-cinnamon">
  <div class="back">
    <div class="mark">RK<br>Buildworks</div>
    <p class="tagline">Your project is our business</p>
    <p class="url">www.rkbuildworks.example</p>
  </div>
  <div class="front">
    <svg viewBox="0 0 386 226" aria-hidden="true">
      <path d="M322 0H386V226H228Q360 150 322 0Z" fill="var(--cinnamon)"/>
      <path d="M322 0Q360 150 228 226" fill="none" stroke="var(--mustard)" stroke-width="4"/>
      <path d="M332 0Q368 150 246 226" fill="none" stroke="var(--rose)" stroke-width="3"/>
      <path d="M342 0Q378 150 262 226" fill="none" stroke="var(--orange)" stroke-width="3"/>
      <circle cx="345" cy="172" r="40" fill="var(--cream)"/>
      <text x="345" y="168" text-anchor="middle" font-family="Arimo, sans-serif" font-weight="700" font-size="11" fill="var(--cinnamon)">RK</text>
      <text x="345" y="182" text-anchor="middle" font-family="Arimo, sans-serif" font-weight="700" font-size="11" fill="var(--cinnamon)">Buildworks</text>
    </svg>
    <h1 class="name">LORNA VASQUEL</h1>
    <p class="title">Eng. President</p>
    <p class="services">Commercial &amp; Residential General<br>Construction Kitchen &amp; Bath Design</p>
    <table class="contacts">
      <tr><th>Phone:</th><td>555-304-7718</td></tr>
      <tr><th>Fax:</th><td>555-304-7719</td></tr>
      <tr><th>Cell:</th><td>555-862-3097</td></tr>
      <tr><th>Email</th><td>lorna@rkbuildworks.example</td></tr>
    </table>
  </div>
</section>

<section class="pair opt-mustard">
  <div class="back">
    <div class="mark">RK<br>Buildworks</div>
    <p class="tagline">Your project is our business</p>
    <p class="url">www.rkbuildworks.example</p>
  </div>
  <div class="front">
    <svg viewBox="0 0 386 226" aria-hidden="true">
      <path d="M322 0H386V226H228Q360 150 322 0Z" fill="var(--mustard)"/>
      <path d="M322 0Q360 150 228 226" fill="none" stroke="var(--cinnamon)" stroke-width="4"/>
      <path d="M332 0Q368 150 246 226" fill="none" stroke="var(--rose)" stroke-width="3"/>
      <path d="M342 0Q378 150 262 226" fill="none" stroke="var(--orange)" stroke-width="3"/>
      <circle cx="345" cy="172" r="40" fill="var(--cinnamon)"/>
      <text x="345" y="168" text-anchor="middle" font-family="Arimo, sans-serif" font-weight="700" font-size="11" fill="var(--cream)">RK</text>
      <text x="345" y="182" text-anchor="middle" font-family="Arimo, sans-serif" font-weight="700" font-size="11" fill="var(--cream)">Buildworks</text>
    </svg>
    <h1 class="name">LORNA VASQUEL</h1>
    <p class="title">Eng. President</p>
    <p class="services">Commercial &amp; Residential General<br>Construction Kitchen &amp; Bath Design</p>
    <table class="contacts">
      <tr><th>Phone:</th><td>555-304-7718</td></tr>
      <tr><th>Fax:</th><td>555-304-7719</td></tr>
      <tr><th>Cell:</th><td>555-862-3097</td></tr>
      <tr><th>Email</th><td>lorna@rkbuildworks.example</td></tr>
    </table>
  </div>
</section>

<section class="pair opt-mustard-light">
  <div class="back">
    <div class="mark">RK<br>Buildworks</div>
    <p class="tagline">Your project is our business</p>
    <p class="url">www.rkbuildworks.example</p>
  </div>
  <div class="front">
    <svg viewBox="0 0 386 226" aria-hidden="true">
      <path d="M322 0H386V226H228Q360 150 322 0Z" fill="var(--mustard)"/>
      <path d="M322 0Q360 150 228 226" fill="none" stroke="var(--cinnamon)" stroke-width="4"/>
      <path d="M332 0Q368 150 246 226" fill="none" stroke="var(--rose)" stroke-width="3"/>
      <path d="M342 0Q378 150 262 226" fill="none" stroke="var(--orange)" stroke-width="3"/>
      <circle cx="345" cy="172" r="40" fill="var(--cream)"/>
      <text x="345" y="168" text-anchor="middle" font-family="Arimo, sans-serif" font-weight="700" font-size="11" fill="var(--cinnamon)">RK</text>
      <text x="345" y="182" text-anchor="middle" font-family="Arimo, sans-serif" font-weight="700" font-size="11" fill="var(--cinnamon)">Buildworks</text>
    </svg>
    <h1 class="name">LORNA VASQUEL</h1>
    <p class="title">Eng. President</p>
    <p class="services">Commercial &amp; Residential General<br>Construction Kitchen &amp; Bath Design</p>
    <table class="contacts">
      <tr><th>Phone:</th><td>555-304-7718</td></tr>
      <tr><th>Fax:</th><td>555-304-7719</td></tr>
      <tr><th>Cell:</th><td>555-862-3097</td></tr>
      <tr><th>Email</th><td>lorna@rkbuildworks.example</td></tr>
    </table>
  </div>
</section>

<section class="pair opt-cocoa">
  <div class="back">
    <div class="mark">RK<br>Buildworks</div>
    <p class="tagline">Your project is our business</p>
    <p class="url">www.rkbuildworks.example</p>
  </div>
  <div class="front">
    <svg viewBox="0 0 386 226" aria-hidden="true">
      <path d="M336 0H386V226H246Q372 150 336 0Z" fill="var(--cocoa)"/>
      <path d="M322 0Q360 150 228 226" fill="none" stroke="var(--cinnamon)" stroke-width="4"/>
      <path d="M332 0Q368 150 246 226" fill="none" stroke="var(--mustard)" stroke-width="3"/>
      <path d="M342 0Q378 150 262 226" fill="none" stroke="var(--orange)" stroke-width="3"/>
      <circle cx="345" cy="172" r="40" fill="var(--cream)"/>
      <text x="345" y="168" text-anchor="middle" font-family="Arimo, sans-serif" font-weight="700" font-size="11" fill="var(--cinnamon)">RK</text>
      <text x="345" y="182" text-anchor="middle" font-family="Arimo, sans-serif" font-weight="700" font-size="11" fill="var(--cinnamon)">Buildworks</text>
    </svg>
    <h1 class="name">LORNA VASQUEL</h1>
    <p class="title">Eng. President</p>
    <p class="services">Commercial &amp; Residential General<br>Construction Kitchen &amp; Bath Design</p>
    <table class="contacts">
      <tr><th>Phone:</th><td>555-304-7718</td></tr>
      <tr><th>Fax:</th><td>555-304-7719</td></tr>
      <tr><th>Cell:</th><td>555-862-3097</td></tr>
      <tr><th>Email:</th><td>lorna@rkbuildworks.example</td></tr>
    </table>
  </div>
</section>

</body>
</html>
```